KLN Productions Biz Card 2014-1

I own a small business whose primary function is Professional Fashion and Commercial Photography and has a secondary function of Talent Management of Models/Actors. I've used Crelloband in the past to print my own design, but I'd like something a bit more topical, fresh and done by an artist instead of a photographer (me).

My company logo is included with a few selected horizontal (landscape) photos of some of my models--I'd like to use a single model photo as the background for the entire card, either in color or converted to black and white, at opacity enough to see the photo but not too much to obscure any text or the company logo, or use a photo as a share of the card (not the entire background), or use all the three models on the card in some manor... Our company colors are white, black, grey-silver and red.

Industry/Entity Type

Small Business

Contact Information for Business Card

Dorian Valstead, Owner
KLN Productions
PO Box 7316
Brattleboro VT 05871-7316
(860) 555-4172
dori@klnstudiosample,.com

```html
<!DOCTYPE html>
<html lang="en">
<head>
<meta charset="utf-8">
<title>KLN Productions Business Card</title>
<link rel="stylesheet" href="https://fonts.googleapis.com/css2?family=Open+Sans:wght@400;600&display=swap">
<style>
  :root {
    --backdrop: #e6e4e8;
    --card-white: #ffffff;
    --ink: #1a1a1a;
    --brand-red: #e0261f;
    --silver: #8f8a85;
    --photo-a: #5d6a6e;
    --photo-b: #6b4a3e;
    --photo-c: #b3322c;
  }
  * { margin: 0; padding: 0; box-sizing: border-box; }
  html, body {
    width: 1200px; height: 1000px; overflow: hidden;
    background: var(--backdrop);
    font-family: "Open Sans", Arial, sans-serif;
    color: var(--ink);
  }
  .card {
    position: absolute; left: 265px; width: 665px; height: 397px;
    box-shadow: 0 4px 14px rgba(0,0,0,0.25);
    overflow: hidden;
  }
  .card-front { top: 73px; background: var(--card-white); }
  .card-back { top: 532px; }

  .brand {
    position: absolute; display: flex; align-items: center; gap: 14px;
    font-weight: 600; font-size: 44px; letter-spacing: 1px; white-space: nowrap;
  }
  .card-front .brand { left: 62px; top: 95px; color: var(--ink); }
  .brand-square { width: 38px; height: 38px; background: var(--brand-red); flex: none; }

  .contact-name {
    position: absolute; right: 68px; top: 224px;
    font-weight: 600; font-size: 18px;
  }
  .contact-details {
    position: absolute; right: 68px; top: 267px;
    text-align: right; font-size: 16px; line-height: 23.5px;
  }
  .tagline {
    position: absolute; left: 25px; top: 330px;
    font-size: 16px; line-height: 23.5px;
  }

  .model-photo {
    position: absolute; inset: 0;
    background: linear-gradient(100deg, var(--photo-a) 0%, var(--photo-b) 45%, var(--photo-c) 100%);
  }
  .card-back .brand { left: 140px; top: 300px; color: var(--card-white); font-size: 40px; }
</style>
</head>
<body>
  <section class="card card-front">
    <div class="brand"><span class="brand-square"></span>KLN Productions</div>
    <p class="contact-name">Dorian Valstead &nbsp;|&nbsp; Owner</p>
    <p class="contact-details">
      (860) 555-4172<br>
      dori@klnstudiosample.com<br>
      PO Box 7316 Brattleboro VT
    </p>
    <p class="tagline">Pro Fashion &amp; Commercial Photography<br>and Talent Management</p>
  </section>

  <section class="card card-back">
    <div class="model-photo" role="img" aria-label="Collage of four portrait photos of young male models in diagonal strips"></div>
    <div class="brand"><span class="brand-square"></span>KLN Productions</div>
  </section>
</body>
</html>
```